A 'new law' boutique Australian law firm that provides specialist employment law and people managem

We value helping clients create results with respect workplaces. What differentiates us is we provide actionable training in understanding and dealing with people and ensure legal compliance fits with this approach. We would like a fresh approach to our training overview documents that we currently use in our current law firm (6 attached). Please use pictures, symbols etc consistent with our non-traditional law approach that captures the approach of each training session.. Attached is the logo and draft letterhead for Birchwell Legal which will launch soon.

Target Market(s)

HR Managers and in-house lawyers (non employment specialists) in mid-large Australian companies that are progressive with a relationship based approach to managing employee behaviours and disputes.

Industry/Entity Type

Human Resource

Font styles to use
Sans Serif

Colors
3176b5
33a6d7

Requirements
Must have
• 1 or 2 page PDF for each of the 6 documents that the wording supplied goes into your design which will be pretty similar as we want consistency with our documents

```html
<!DOCTYPE html>
<html lang="en">
<head>
<meta charset="utf-8">
<title>Co-Operatively Compliant Workplaces – Birchwell Legal</title>
<link rel="stylesheet" href="https://fonts.googleapis.com/css2?family=Roboto+Slab:wght@300;400;500;600&display=swap">
<style>
  :root {
    --ink: #2b2b2b;
    --panel-dark: #2d2d2f;
    --white: #ffffff;
    --brand-blue: #3176b5;
    --sky: #33a6d7;
    --sky-bright: #4ec0ee;
    --sky-soft: #82d1f3;
    --sky-pale: #dcf1fb;
    --heading-dark: #2f2f31;
    --ring-grey: #6d6e70;
  }
  * { margin: 0; padding: 0; box-sizing: border-box; }
  html, body { width: 848px; height: 1200px; overflow: hidden; background: var(--white); }
  body { font-family: "Roboto Slab", Rockwell, Georgia, serif; font-weight: 300; color: var(--ink); }

  .sheet { position: relative; width: 848px; height: 1200px; overflow: hidden; }

  /* Left column */
  .intro-panel {
    position: absolute; left: 0; top: 0; width: 505px; height: 885px;
    background: var(--panel-dark); color: var(--white);
  }
  .brand { position: absolute; right: 49px; top: 98px; display: flex; align-items: center; gap: 10px; }
  .brand-mark { width: 18px; height: 18px; border-radius: 50%; background: var(--sky-bright); }
  .brand-name { font-size: 27px; font-weight: 500; color: var(--sky-bright); line-height: 1; }

  .course-title { position: absolute; right: 49px; top: 208px; text-align: right; font-weight: 500; font-size: 34px; line-height: 49px; }
  .course-title .line-1 { color: var(--white); }
  .course-title .line-2 { color: var(--sky-bright); }

  .training-need { position: absolute; right: 49px; top: 320px; width: 420px; text-align: right; }
  .section-label { font-size: 20px; font-weight: 500; color: var(--sky-bright); margin-bottom: 12px; }
  .training-need p { font-size: 11.5px; line-height: 17px; margin-bottom: 4px; }
  .training-need ol { list-style: none; font-size: 11.5px; line-height: 17px; margin-bottom: 4px; }

  .emblem {
    position: absolute; left: 80px; top: 811px; width: 140px; height: 140px; border-radius: 50%;
    background: var(--white); display: flex; align-items: center; justify-content: center;
  }
  .emblem-art { width: 112px; height: 112px; border-radius: 50%; background: var(--sky-bright); border: 6px solid var(--ring-grey); }

  .outcomes { position: absolute; left: 60px; top: 955px; width: 400px; }
  .outcomes h2 { font-size: 20px; font-weight: 500; color: var(--brand-blue); margin-bottom: 12px; }
  .outcomes .lead { font-size: 11.8px; font-weight: 600; margin-bottom: 4px; }
  .outcomes ol { list-style: none; font-size: 11.8px; line-height: 17px; }
  .outcomes li { padding-left: 12px; text-indent: -12px; margin-bottom: 4px; }

  /* Right column */
  .overview {
    position: absolute; left: 505px; top: 0; width: 343px; height: 1200px;
    border-left: 1px solid var(--brand-blue);
  }
  .module { padding: 0 28px 0 40px; color: var(--heading-dark); overflow: hidden; }
  .module h3 { font-size: 16px; font-weight: 400; line-height: 21px; margin-bottom: 6px; }
  .module ul { list-style: none; font-size: 11.8px; line-height: 17px; }
  .module li { padding-left: 9px; text-indent: -9px; margin-bottom: 4px; }
  .module li::before { content: "• "; }

  .module--bright { background: var(--sky-bright); }
  .module--soft { background: var(--sky-soft); }
  .module--pale { background: var(--sky-pale); }
  .module--bright li, .module--soft li { color: var(--white); }
  .module--pale li { color: var(--heading-dark); }

  .m1 { height: 258px; padding-top: 34px; }
  .m2 { height: 198px; padding-top: 30px; }
  .m3 { height: 299px; padding-top: 30px; }
  .m4 { height: 290px; padding-top: 30px; }
  .m5 { height: 155px; padding-top: 28px; }

  .overview-title { font-size: 21px; font-weight: 500; color: var(--brand-blue); margin: 0 0 6px -4px; }
</style>
</head>
<body>
<main class="sheet">
  <section class="intro-panel">
    <div class="brand">
      <span class="brand-mark"></span>
      <span class="brand-name">Birchwell Legal</span>
    </div>

    <h1 class="course-title">
      <span class="line-1">Co-Operatively</span><br>
      <span class="line-2">Compliant Workplaces</span>
    </h1>

    <div class="training-need">
      <h2 class="section-label">Training Need</h2>
      <p>Unresolved conflict often builds and leads to costly claims that result in the right people leaving, reduced productivity and low morale.</p>
      <p>There have been major advances in laws protecting diversity and a real push towards inclusiveness. This has coincided with rapid changes to the workforce and diversity being desirable. So then, what’s the problem?</p>
      <p>Why do record payouts keep being broken for sexual harassment and discrimination claims?</p>
      <p>Why has there been a social media explosion on bullying and bad behaviour?</p>
      <p>Traditional processes just aren’t working. They are usually:</p>
      <ol>
        <li>a) unnecessarily formal;</li>
        <li>b) focused on being seen to be doing something than actually doing something effective;</li>
        <li>c) adversarial; and</li>
        <li>d) responsible for creating outcomes which range from ‘nothing really changes’ to an ‘overkill’.</li>
      </ol>
      <p>When people don’t know what the rules are they are more focused on not getting it wrong rather than getting it right.</p>
      <p>For organisations who are frustrated by an overemphasis on language to avoid causing offence and a fear of legal claims, this training offers a relationship-based approach to compliance. Unlike traditional training, this training focuses on ground rules for practically understanding workplace behaviour laws and guidelines for dealing with inevitable conflict.</p>
      <p>This training will benefit workplaces where there is unresolved team conflict or lack of self-awareness as to the impact of behaviours on others.</p>
    </div>
  </section>

  <div class="emblem"><div class="emblem-art" role="img" aria-label="Handshake icon"></div></div>

  <section class="outcomes">
    <h2>Learning Outcomes</h2>
    <p class="lead">Participants will apply the learnings to understand:</p>
    <ol>
      <li>1. What diversity and inclusiveness means and why it is a ‘must have’ for success and not simply a ‘must avoid’ for compliance.</li>
      <li>2. Different perspectives and that building professional relationships is crucial for effective performance and not being ‘proved right’.</li>
      <li>3. Lawful and effective workplace behaviour in terms of what’s ok, what’s not ok, what’s grey and how to deal with that.</li>
      <li>4. How to be more comfortable with uncomfortable conversations that need to occur to work cooperatively and achieve results and not avoidance for fear of legal claims.</li>
    </ol>
  </section>

  <aside class="overview">
    <section class="module module--bright m1">
      <h2 class="overview-title">Training Overview</h2>
      <h3>Social Safety is Basic Biology</h3>
      <ul>
        <li>What is a socially safe workplace and why it matters</li>
        <li>A WH&amp;S approach to cooperative workplace behaviour</li>
        <li>Diversity: what does it mean and its benefits</li>
        <li>Balancing act: valuing different perspectives and shared values</li>
      </ul>
    </section>
    <section class="module module--soft m2">
      <h3>Building Effective Relationships: Trust and Respect</h3>
      <ul>
        <li>The 4 natural work styles: self-awareness and understanding others</li>
        <li>Don’t avoid the conversation: creating safe spaces to resolve conflict before ‘pinch points’ become a crunch</li>
      </ul>
    </section>
    <section class="module module--pale m3">
      <h3>Ground Rules:<br>Understanding the workplace behaviour legal framework</h3>
      <ul>
        <li>What is and isn’t bullying, discrimination, sexual harassment, adverse action and victimisation</li>
        <li>Appropriate versus inappropriate behaviour</li>
        <li>What is and isn’t reasonable management action</li>
        <li>Unfair dismissal, adverse action, discrimination, bullying and stress claims</li>
        <li>Individual legal liability</li>
      </ul>
    </section>
    <section class="module module--bright m4">
      <h3>Guidelines: How to avoid unlawful behaviour and generally be effective in a diverse workplace</h3>
      <ul>
        <li>Not a ‘one size fits all’: Applying the understanding of natural workstyles to identify and deal with potential bullying, sexual harassment and discrimination</li>
        <li>Understanding your why: identify and challenge your biases</li>
        <li>Risk management: understanding relationships and context</li>
      </ul>
    </section>
    <section class="module module--soft m5">
      <h3>Activities</h3>
      <ul>
        <li>Scenarios to identify potential unlawful or inappropriate behaviour and reasonable action to raise and respond</li>
        <li>Questionnaire to demonstrate due diligence</li>
      </ul>
    </section>
  </aside>
</main>
</body>
</html>
```